Brisbane IT support business needs our first website

Hi All,

We are after a new website design for our IT solutions and support business.The business name is Harbourline Computing Services Group, or HCSG for short. We provide a range of solutions and services within the IT space.

I would like to utilize the two colours in our business logo I have uploaded.

I understand this is initially for the design only aspect of the site, but I would like to engage the winner to finish coding the website and finalize after also.

Target Market(s)

Other businesses owners and home users.

Industry/Entity Type

Business

Requirements
Must have
• Nice clean and functional design utilizing our business colours from the logo.

```html
<!DOCTYPE html>
<html lang="en">
<head>
<meta charset="utf-8">
<title>Harbourline Computing Services Group</title>
<link href="https://fonts.googleapis.com/css2?family=Lato:ital,wght@0,300;0,400;0,700;0,900;1,400;1,700&family=Montserrat:wght@500;600&display=swap" rel="stylesheet">
<style>
:root{
  --navy:#0e4a63;
  --orange:#ef7f22;
  --ink:#333;
  --muted:#666;
  --quote-bg:#f1f1f1;
  --footer:#222;
  --footer-mid:#2e2e2e;
  --footer-base:#111;
  --white:#fff;
}
*{margin:0;padding:0;box-sizing:border-box}
html,body{width:1200px;height:1108px;overflow:hidden;background:var(--white);font-family:"Lato",sans-serif;color:var(--ink)}
.page{position:relative;width:1200px;height:1108px}

/* header */
.site-header{position:absolute;left:0;top:0;width:1200px;height:122px}
.brand{position:absolute;left:131px;top:44px;display:flex;align-items:center;gap:10px}
.brand-mark{width:22px;height:22px;background:var(--orange)}
.brand-name{font-family:"Montserrat",sans-serif;font-weight:600;font-size:26px;line-height:30px;color:var(--navy)}
.contact-top{position:absolute;top:18px;right:60px;display:flex;align-items:center;gap:18px}
.contact-item{display:flex;align-items:center;gap:10px;color:var(--navy);font-family:"Montserrat",sans-serif;font-weight:600}
.contact-item .mail{font-size:14px}
.contact-item .phone{font-size:19px}
.contact-icon{width:34px;height:34px}
.main-nav{position:absolute;right:60px;top:82px;display:flex;font-family:"Montserrat",sans-serif;font-weight:600;font-size:13.6px;color:#333}
.main-nav a{color:inherit;text-decoration:none;padding:0 15px;border-left:1px solid #ccc;line-height:14px}
.main-nav a:first-child{border-left:none}
.main-nav a:last-child{padding-right:0}
.main-nav a.active{color:var(--orange);position:relative}
.main-nav a.active::after{content:"";position:absolute;left:18px;right:15px;bottom:-10px;height:3px;background:var(--orange)}

/* hero */
.hero{position:absolute;left:0;top:122px;width:1200px;height:516px;background:linear-gradient(180deg,#3f6f88 0%,#4b7c93 45%,#3b6b7f 75%,#2c5566 100%)}
.hero-photo{position:absolute;inset:0;background:linear-gradient(90deg,rgba(20,60,80,.35),rgba(20,60,80,0) 30%,rgba(20,60,80,0) 70%,rgba(20,60,80,.35))}
.hero-title{position:absolute;left:0;width:1200px;top:64px;text-align:center;color:var(--white)}
.hero-title .line1{font-size:58px;line-height:70px;font-weight:300}
.hero-title .line1 b{color:var(--orange);font-weight:700}
.hero-title .line1 span{color:var(--orange)}
.hero-title .line2{font-size:48px;line-height:58px;font-weight:300;text-shadow:0 2px 3px rgba(0,0,0,.4)}
.hero-rule{position:absolute;left:461px;top:200px;width:278px;height:1px;background:rgba(255,255,255,.55)}
.feature{position:absolute;top:274px;width:169px;height:178px;background:rgba(40,120,150,.55);border-radius:3px;text-align:center;color:var(--white)}
.feature-icon{margin:17px auto 0;width:80px;height:80px;border-radius:50%;background:var(--orange);display:flex;align-items:center;justify-content:center}
.feature-name{margin-top:16px;font-family:"Montserrat",sans-serif;font-weight:600;font-size:19.5px;line-height:25px}
.slider-arrow{position:absolute;top:340px;width:24px;height:48px}

/* reviews */
.reviews{position:absolute;left:0;top:638px;width:1200px;height:302px}
.section-title{position:absolute;width:1200px;top:37px;text-align:center;font-family:"Montserrat",sans-serif;font-weight:600;font-size:28px;color:var(--navy)}
.section-lead{position:absolute;width:1200px;top:73px;text-align:center;font-size:15.5px;color:var(--muted)}
.divider{position:absolute;top:102px;left:356px;width:488px;height:18px}
.quote-box{position:absolute;left:131px;top:137px;width:804px;height:98px;background:var(--quote-bg);clip-path:polygon(0 0,767px 0,804px 36px,804px 98px,0 98px)}
.quote-tail{position:absolute;left:838px;top:235px;width:0;height:0;border-left:12px solid transparent;border-right:12px solid transparent;border-top:13px solid var(--quote-bg)}
.quote-text{position:absolute;left:149px;top:150px;width:752px;font-style:italic;font-size:13.6px;line-height:24px;color:#444;text-indent:34px}
.quote-mark{position:absolute;left:153px;top:150px;font-family:"Lato",sans-serif;font-weight:900;font-size:48px;line-height:44px;color:#bbb}
.avatar{position:absolute;left:931px;top:129px;width:120px;height:120px;border-radius:50%;background:linear-gradient(160deg,#d9e4ec,#9fb1bd);border:5px solid #e6e6e6;box-shadow:0 0 0 1px #ccc}
.reviewer{position:absolute;left:600px;width:335px;top:255px;text-align:right;font-style:italic;font-weight:700;font-size:13px;color:#333}

/* footer */
.footer{position:absolute;left:0;top:940px;width:1200px;height:103px;background:var(--footer);color:var(--white)}
.footer-social-bg{position:absolute;left:501px;top:0;width:197px;height:103px;background:var(--footer-mid)}
.newsletter-icon{position:absolute;left:131px;top:24px;width:50px;height:48px}
.footer-heading{position:absolute;font-weight:700;font-size:16px}
.signup{position:absolute;left:197px;top:48px;display:flex;height:27px}
.signup-input{width:170px;background:var(--white);color:#555;font-style:italic;font-size:11px;line-height:27px;padding-left:11px}
.signup-btn{width:91px;background:var(--orange);color:var(--white);font-weight:700;font-size:13.5px;line-height:27px;text-align:center}
.social{position:absolute;left:530px;top:47px;display:flex;gap:9px}
.social span{width:29px;height:29px;border-radius:50%;background:var(--white)}
.address{position:absolute;left:755px;top:20px;font-size:14px;line-height:18px;color:#eee}
.footer-line{position:absolute;display:flex;align-items:center;gap:16px;font-size:14px;color:#eee}
.footer-line b{font-weight:700}
.copyright{position:absolute;left:0;top:1043px;width:1200px;height:65px;background:var(--footer-base);color:#ddd;text-align:center;font-size:14px;line-height:65px}
</style>
</head>
<body>
<div class="page">

  <header class="site-header">
    <div class="brand">
      <div class="brand-mark"></div>
      <div class="brand-name">HCSG</div>
    </div>

    <div class="contact-top">
      <div class="contact-item">
        <svg class="contact-icon" viewBox="0 0 34 34"><path d="M2 2h24l6 15-6 15H2z" fill="none" stroke="#ef7f22" stroke-width="2"/><rect x="7" y="11" width="15" height="11" fill="#ef7f22"/><path d="M7 11l7.5 6 7.5-6" fill="none" stroke="#fff" stroke-width="1.5"/></svg>
        <span class="mail">hello@harbourlinecs.com</span>
      </div>
      <div class="contact-item">
        <svg class="contact-icon" viewBox="0 0 34 34"><path d="M2 2h24l6 15-6 15H2z" fill="none" stroke="#ef7f22" stroke-width="2"/><rect x="10" y="8" width="10" height="17" rx="1.5" fill="#ef7f22"/><rect x="12" y="10" width="6" height="8" fill="#fff"/></svg>
        <span class="phone">123-456-7890</span>
      </div>
    </div>

    <nav class="main-nav">
      <a class="active" href="#">HOME</a>
      <a href="#">ABOUT</a>
      <a href="#">SERVICES</a>
      <a href="#">TECHNOLOGY</a>
      <a href="#">SOLUTIONS</a>
      <a href="#">SUPPORT</a>
      <a href="#">CONTACT</a>
    </nav>
  </header>

  <section class="hero">
    <div class="hero-photo" role="img" aria-label="City skyline photograph with high-rise towers behind a riverside park, tinted blue"></div>
    <div class="hero-title">
      <div class="line1"><b>Success</b> <span>With</span></div>
      <div class="line2">Our Creative Solutions</div>
    </div>
    <div class="hero-rule"></div>

    <svg class="slider-arrow" style="left:131px" viewBox="0 0 24 48"><path d="M22 2L2 24l20 22" fill="none" stroke="rgba(255,255,255,.7)" stroke-width="2"/></svg>
    <svg class="slider-arrow" style="left:1045px" viewBox="0 0 24 48"><path d="M2 2l20 22L2 46" fill="none" stroke="rgba(255,255,255,.7)" stroke-width="2"/></svg>

    <div class="feature" style="left:187px">
      <div class="feature-icon">
        <svg width="44" height="44" viewBox="0 0 44 44"><path d="M30 4a10 10 0 0 0-9 14L5 34a4 4 0 0 0 5 5l16-16a10 10 0 0 0 14-9l-6 6-6-2-2-6 6-6z" fill="#fff"/></svg>
      </div>
      <div class="feature-name">IT<br>Support</div>
    </div>

    <div class="feature" style="left:403px">
      <div class="feature-icon">
        <svg width="44" height="46" viewBox="0 0 44 46"><ellipse cx="22" cy="8" rx="20" ry="6" fill="#fff"/><path d="M2 13c0 3 9 6 20 6s20-3 20-6v8c0 3-9 6-20 6S2 24 2 21z" fill="#fff"/><path d="M2 25c0 3 9 6 20 6s20-3 20-6v8c0 3-9 6-20 6S2 36 2 33z" fill="#fff"/></svg>
      </div>
      <div class="feature-name">Data<br>Management</div>
    </div>

    <div class="feature" style="left:628px">
      <div class="feature-icon">
        <svg width="50" height="40" viewBox="0 0 50 40"><path d="M2 10l8-6 14 4 6-3 18 6-4 14-10 9-6-3-6 4-8-7-8-6z" fill="#fff"/><path d="M20 22l6 5M24 18l7 6M28 15l7 6" stroke="#ef7f22" stroke-width="2"/></svg>
      </div>
      <div class="feature-name">Customer<br>Relationship</div>
    </div>

    <div class="feature" style="left:844px">
      <div class="feature-icon">
        <svg width="36" height="44" viewBox="0 0 36 44"><path d="M8 20v-7a10 10 0 0 1 20 0v7" fill="none" stroke="#fff" stroke-width="5"/><rect x="2" y="19" width="32" height="23" rx="2" fill="#fff"/></svg>
      </div>
      <div class="feature-name">100%<br>Secure</div>
    </div>
  </section>

  <section class="reviews">
    <h2 class="section-title">Our Customer Review</h2>
    <p class="section-lead">Lorem ipsum dolor sit amet, consectetur Donec a consequat mag&nbsp; Aenean eu velit&nbsp; Aenean sollicitudin</p>
    <svg class="divider" viewBox="0 0 488 18"><line x1="0" y1="9" x2="214" y2="9" stroke="#cfcfcf"/><line x1="274" y1="9" x2="488" y2="9" stroke="#cfcfcf"/><g fill="#c8c8c8"><path d="M227 2l2 5h5l-4 3 2 5-5-3-5 3 2-5-4-3h5z"/><path d="M244 2l2 5h5l-4 3 2 5-5-3-5 3 2-5-4-3h5z"/><path d="M261 2l2 5h5l-4 3 2 5-5-3-5 3 2-5-4-3h5z"/></g></svg>

    <div class="quote-box"></div>
    <div class="quote-tail"></div>
    <div class="quote-mark">&ldquo;</div>
    <p class="quote-text">Lorem sum dolor sit amet, consectetuer adipiscing elit, sed diam nonummy nibh euismod tincidunt ut laoreet re agn aliqam erat volutpat wisi enim ad minim veniam, quis nostrud exerci tation ullamcorper suscipit lobortis nisl ut aliquip modo conseuatis autem vel eum iriure dolor in hendrerit in vulputate velit esse molestie consequat, vel illum dolore eu.</p>
    <div class="avatar" role="img" aria-label="Portrait photograph of the reviewing customer"></div>
    <div class="reviewer">Marcus, Northgate Labs , USA</div>
  </section>

  <footer class="footer">
    <div class="footer-social-bg"></div>

    <svg class="newsletter-icon" viewBox="0 0 50 48"><path d="M1 18L25 2l24 16v29H1z" fill="#fff"/><rect x="10" y="6" width="30" height="26" fill="#222"/><rect x="12" y="8" width="26" height="22" fill="#fff"/><path d="M1 18l24 16 24-16v29H1z" fill="#fff" stroke="#222" stroke-width="2"/><path d="M1 47l18-14M49 47L31 33" stroke="#222" stroke-width="2"/></svg>
    <div class="footer-heading" style="left:199px;top:21px">Sign up for Newsletter</div>
    <div class="signup">
      <div class="signup-input">Your Email Address</div>
      <div class="signup-btn">SUBSCRIBE</div>
    </div>

    <div class="footer-heading" style="left:530px;top:21px">Follow us on</div>
    <div class="social" aria-label="Social links">
      <span></span><span></span><span></span><span></span>
    </div>

    <svg style="position:absolute;left:735px;top:23px" width="12" height="17" viewBox="0 0 12 17"><path d="M6 0a6 6 0 0 1 6 6c0 4-6 11-6 11S0 10 0 6a6 6 0 0 1 6-6z" fill="#fff"/><circle cx="6" cy="6" r="2.2" fill="#222"/></svg>
    <div class="address">123&nbsp; Lorem Sum Dolor<br>Sit Amet Consectuer<br>Adipiscing Elit</div>

    <div class="footer-line" style="left:917px;top:22px">
      <svg width="10" height="16" viewBox="0 0 10 16"><rect x="0.5" y="0.5" width="9" height="15" rx="1.5" fill="none" stroke="#fff"/><rect x="2" y="2.5" width="6" height="9" fill="#fff"/></svg>
      <b>(123) 456-7890</b>
    </div>
    <div class="footer-line" style="left:915px;top:57px">
      <svg width="14" height="10" viewBox="0 0 14 10"><rect width="14" height="10" fill="#fff"/><path d="M0 0l7 6 7-6" fill="none" stroke="#222" stroke-width="1.2"/></svg>
      <span>info@harbourlinecs.com</span>
    </div>
  </footer>

  <div class="copyright">© 2014 Harbourline Computing Services Group. All Rights Reserved.</div>
</div>
</body>
</html>
```